Postcard for Antique Furniture Restorer

My business is to restore antique furniture. I am based in Sydney, Australia.

I will be using this postcard to promote my business.
I will give it to customers like a With Compliments card.

Sometimes I will be writing information on the back of the card.

Design for Postcard Size eg 148 X 105mm

Front of card:

Attached are images of Antique furniture - please use ONLY 1 of the 3 images.
Deep etch the image on a white or cream background.

On front of card add these words:
Grainward Keepsakes
antique furniture restoration

Antiques travel through time, seeing generations of families
Through time they remain - they tell a continuing story
Be part of the journey

Back of postcard:
(leave space for notes to be handwritten)

Add these words:

Grainward Keepsakes
Corin Maddaford
mobile 0473 582 316
www.oakmendcraftery.com.au

Industry/Entity Type

Business

Font styles to use
Serif
Sans Serif

Colors
fefdec
ffffff

Requirements
Must have
• Use only 1 image. Image must be deep etched.

```html
<!DOCTYPE html>
<html lang="en">
<head>
<meta charset="utf-8">
<title>Grainward Keepsakes – Postcard</title>
<link rel="stylesheet" href="https://fonts.googleapis.com/css2?family=Open+Sans:wght@700&family=Pinyon+Script&family=Crimson+Text:ital,wght@0,400;0,700;1,400;1,700&display=swap">
<style>
  :root {
    --stage: #9a9a9a;
    --parchment-light: #efe3c8;
    --parchment-mid: #dcc7a0;
    --parchment-dark: #b8955e;
    --cream: #f3ebdc;
    --cream-deep: #ece1cc;
    --flourish: #f8f3ea;
    --brown: #5a2b12;
    --ink: #4a2410;
    --wood-light: #a8472a;
    --wood-dark: #4e1a0e;
  }
  * { margin: 0; padding: 0; box-sizing: border-box; }
  html, body { width: 1200px; height: 646px; overflow: hidden; }
  body { background: var(--stage); position: relative; }

  .card {
    position: absolute;
    top: 112px;
    width: 568px;
    height: 402px;
    overflow: hidden;
  }
  .card--front {
    left: 26px;
    background: radial-gradient(ellipse at 45% 40%, var(--parchment-light) 0%, var(--parchment-mid) 60%, var(--parchment-dark) 100%);
  }
  .card--back {
    left: 612px;
    background: linear-gradient(120deg, var(--cream) 0%, var(--cream-deep) 100%);
  }

  .flourish {
    position: absolute;
    background: radial-gradient(ellipse at center, var(--flourish) 0%, rgba(248,243,234,0) 70%);
    opacity: .7;
  }
  .card--front .flourish { left: 0; top: 0; width: 568px; height: 402px; opacity: .35; }
  .card--back .flourish--top { left: -40px; top: -30px; width: 320px; height: 190px; }
  .card--back .flourish--bottom { left: -20px; top: 250px; width: 330px; height: 180px; }

  .furniture-photo {
    position: absolute;
    left: 308px;
    top: 24px;
    width: 228px;
    height: 332px;
    background: linear-gradient(160deg, var(--wood-light) 0%, var(--wood-dark) 100%);
    border-radius: 4px 4px 2px 2px;
  }

  .brand-block {
    position: absolute;
    text-align: center;
    color: var(--brown);
  }
  .card--front .brand-block { left: 16px; width: 300px; top: 82px; }
  .card--back .brand-block { left: 20px; width: 270px; top: 128px; }

  .brand-name {
    font-family: "Open Sans", Arial, sans-serif;
    font-weight: 700;
    font-size: 25px;
    line-height: 30px;
  }
  .brand-tagline {
    font-family: "Pinyon Script", cursive;
    font-size: 21px;
    line-height: 26px;
    color: var(--ink);
  }

  .story {
    margin-top: 14px;
    font-family: "Crimson Text", Georgia, serif;
    font-style: italic;
    font-size: 16px;
    line-height: 21px;
    color: var(--ink);
  }
  .story strong { font-weight: 700; }

  .contact {
    margin-top: 22px;
    font-family: "Crimson Text", Georgia, serif;
    color: var(--ink);
  }
  .contact-name { font-style: italic; font-size: 19px; line-height: 24px; }
  .contact-phone { font-weight: 700; font-size: 19px; line-height: 26px; color: var(--brown); }
  .contact-web { font-weight: 700; font-size: 13.5px; line-height: 22px; }
</style>
</head>
<body>
  <section class="card card--front">
    <div class="flourish" role="img" aria-label="Faint cream floral flourishes on aged parchment"></div>
    <div class="furniture-photo" role="img" aria-label="Deep-etched antique carved wooden armoire with burl panels"></div>
    <div class="brand-block">
      <p class="brand-name">Grainward Keepsakes</p>
      <p class="brand-tagline">Antique Furniture Restoration</p>
      <p class="story">
        Antiques travel through time, seeing<br>
        generations of families<br>
        Through time they remain - they tell a<br>
        continuing story<br>
        <strong>Be part of the journey</strong>
      </p>
    </div>
  </section>

  <section class="card card--back">
    <div class="flourish flourish--top" role="img" aria-label="Cream floral flourish ornament"></div>
    <div class="flourish flourish--bottom" role="img" aria-label="Cream floral flourish ornament"></div>
    <div class="brand-block">
      <p class="brand-name">Grainward Keepsakes</p>
      <p class="brand-tagline">Antique Furniture Restoration</p>
      <div class="contact">
        <p class="contact-name">Corin Maddaford</p>
        <p class="contact-phone">0473 582 316</p>
        <p class="contact-web">www.oakmendcraftery.com.au</p>
      </div>
    </div>
  </section>
</body>
</html>
```